Veterinary Hospital Business Card

We have recently updated our logo and wish to have a business card designed incorporating the new look and flow. We are a full service veterinary hospital also offering laser therapy, boarding, and grooming. Our website is www.marlowpawsvets.com

Industry/Entity Type

Veterinary

```html
<!DOCTYPE html>
<html lang="en">
<head>
<meta charset="utf-8">
<title>Marlow Paws Animal Hospital – Business Card</title>
<link rel="stylesheet" href="https://fonts.googleapis.com/css2?family=Exo+2:wght@400;600;700&display=swap">
<style>
  :root {
    --backdrop: #e4e6e8;
    --card: #ffffff;
    --navy: #3e6e8c;
    --steel: #5b8fae;
    --sky: #7fa9c3;
    --ink: #4a5a66;
    --white: #ffffff;
  }
  * { box-sizing: border-box; margin: 0; padding: 0; }
  html, body {
    width: 1200px; height: 854px; overflow: hidden;
    background: var(--backdrop);
    font-family: "Exo 2", sans-serif;
  }
  .stage {
    position: relative; width: 1200px; height: 854px;
    display: flex; align-items: center; justify-content: center;
  }
  .business-card {
    position: relative; width: 440px; height: 770px;
    background: var(--card);
    overflow: hidden;
    box-shadow: 0 6px 22px rgba(0,0,0,.12);
  }
  .brand {
    position: absolute; top: 82px; left: 0; right: 0;
    display: flex; align-items: center; justify-content: center; gap: 16px;
  }
  .brand-dot {
    width: 42px; height: 42px; border-radius: 50%; flex: none;
    background: var(--navy);
  }
  .brand-name {
    color: var(--navy); font-weight: 700; text-transform: uppercase;
    line-height: 1.04; letter-spacing: 1px;
  }
  .brand-name .line-lg { display: block; font-size: 36px; }
  .brand-name .line-sm { display: block; font-size: 25px; }
  .person {
    position: absolute; top: 292px; left: 0; right: 0; text-align: center;
  }
  .person-name {
    color: var(--steel); font-size: 36px; font-weight: 600;
    letter-spacing: 2px; text-transform: uppercase;
  }
  .person-role {
    color: var(--steel); font-size: 15px; letter-spacing: 2px;
    text-transform: uppercase; margin-top: 2px;
  }
  .contacts {
    position: absolute; top: 402px; left: 44px; right: 24px;
    display: grid; grid-template-columns: 150px 1fr; row-gap: 12px; column-gap: 14px;
  }
  .contact {
    display: flex; align-items: center; gap: 8px;
    color: var(--ink); font-size: 13px; letter-spacing: .5px;
    white-space: nowrap;
  }
  .contact-icon { width: 18px; height: 18px; flex: none; }
  .address-band {
    position: absolute; left: 0; bottom: 0; width: 440px; height: 300px;
  }
  .address {
    position: absolute; left: 0; right: 0; top: 570px; text-align: center;
    color: var(--white); font-size: 27px; font-style: normal;
    letter-spacing: 1.5px; line-height: 1.45;
  }
</style>
</head>
<body>
<main class="stage">
  <article class="business-card">
    <header class="brand">
      <span class="brand-dot"></span>
      <h1 class="brand-name">
        <span class="line-lg">Marlow Paws</span>
        <span class="line-sm">Animal Hospital</span>
      </h1>
    </header>

    <section class="person">
      <h2 class="person-name">Daniel Hart</h2>
      <p class="person-role">General Manager</p>
    </section>

    <section class="contacts">
      <p class="contact">
        <svg class="contact-icon" viewBox="0 0 18 18"><circle cx="9" cy="9" r="9" fill="var(--navy)"/><path d="M6 4.5c.6 0 1.3 1.6 1.3 2s-.8.7-.7 1.1c.3 1 1.2 2 2.2 2.3.4.1.7-.7 1.1-.7s2 .7 2 1.3-.9 1.8-1.8 1.8C7.6 12.3 5.2 9.9 4.7 7.5 4.5 5.6 5.4 4.5 6 4.5z" fill="#fff"/></svg>
        014 827 3390
      </p>
      <p class="contact">
        <svg class="contact-icon" viewBox="0 0 18 18"><circle cx="9" cy="9" r="9" fill="var(--navy)"/><rect x="5" y="6" width="8" height="6" rx="1" fill="none" stroke="#fff" stroke-width="1.2"/><path d="M5.3 6.4 9 9.4l3.7-3" fill="none" stroke="#fff" stroke-width="1.2"/></svg>
        hello@marlowpawsvets.com
      </p>
      <p class="contact">
        <svg class="contact-icon" viewBox="0 0 18 18"><circle cx="9" cy="9" r="9" fill="var(--navy)"/><rect x="6.3" y="4" width="5.4" height="10" rx="1" fill="none" stroke="#fff" stroke-width="1.2"/><circle cx="9" cy="12" r=".7" fill="#fff"/></svg>
        014 827 3391
      </p>
      <p class="contact">
        <svg class="contact-icon" viewBox="0 0 18 18"><circle cx="9" cy="9" r="9" fill="var(--navy)"/><circle cx="9" cy="9" r="4.5" fill="none" stroke="#fff" stroke-width="1.1"/><path d="M4.5 9h9M9 4.5c-2 2.5-2 6.5 0 9M9 4.5c2 2.5 2 6.5 0 9" fill="none" stroke="#fff" stroke-width="1"/></svg>
        www.marlowpawsvets.com
      </p>
    </section>

    <svg class="address-band" viewBox="0 0 440 300" aria-hidden="true">
      <path d="M0 40 Q200 -18 440 58 L440 300 L0 300 Z" fill="var(--navy)"/>
      <rect x="36" y="244" width="368" height="36" rx="18" fill="var(--sky)"/>
    </svg>

    <address class="address">
      42 Kestrel Lane,<br>Marlow Court West
    </address>
  </article>
</main>
</body>
</html>
```